Design a website for a newly developed Delta 8 THC Company

Design a responsive Website with the following goals in mind:
- Built on Wordpress/WooCommerce theme. Please use this when designing for ease of integration.
- Build trust with website visitors with an engaging, informative content driven website, that leads to a conversion of product purchase and repeat business. We will also be driving consumers to businesses that carry our products as well.
- The website will embody a lifestyle feel and make the visitor identify with the content.
- The website will allow for super charged SEO and other digital marketing and advertising strategies and tactics used to increase discovery, awareness, and conversion.
Please see additional goals in the uploaded files.
Target Market(s)
Male/Female 21-
Industry/Entity Type
Cannabis/Hemp
Coding
Coded - Design and coding required
Number of Pages Required
5+ page
Font styles to use
Other font styles liked:
- Montserrat
Look and feel
Each slider illustrates characteristics of the customer's brand and the style your logo design should communicate.

```html
<!DOCTYPE html>
<html lang="en">
<head>
<meta charset="utf-8">
<title>Verdance — Delta 8</title>
<link href="https://fonts.googleapis.com/css2?family=Montserrat:wght@400;500;600;700;800&family=Roboto:wght@300;400;500&display=swap" rel="stylesheet">
<style>
:root{
  --ink:#222222;
  --black:#050505;
  --brown:#8a5236;
  --brown-band:#8c5439;
  --gold:#c9a24c;
  --yellow:#f9e071;
  --muted:#6b6b6b;
  --line:#e3e3e3;
  --white:#ffffff;
  --card-grey:#e4e4e4;
}
*{margin:0;padding:0;box-sizing:border-box}
html,body{width:1200px;height:4044px;overflow:hidden}
body{position:relative;background:var(--white);font-family:"Roboto",Arial,sans-serif;color:var(--ink)}
.abs{position:absolute}
.heading{font-family:"Montserrat",Arial,sans-serif;font-weight:700;text-transform:uppercase;letter-spacing:.5px}
.center{text-align:center;left:0;width:1200px}

/* header */
.site-header{position:absolute;left:0;top:0;width:1200px;height:119px;background:var(--black)}
.topbar{position:absolute;left:420px;top:0;width:780px;height:50px;background:var(--brown);clip-path:polygon(40px 0,100% 0,100% 100%,0 100%)}
.topbar-links{position:absolute;right:55px;top:17px;display:flex;gap:34px;font-size:15px;color:var(--white);font-family:"Montserrat",sans-serif}
.topbar-links span{display:flex;align-items:center;gap:5px}
.brand{position:absolute;display:flex;align-items:center;gap:8px;font-family:"Montserrat",sans-serif;font-weight:600;letter-spacing:4px;color:var(--gold)}
.brand .dot{width:18px;height:18px;border:2px solid var(--gold);border-radius:50%}
.main-nav{position:absolute;right:110px;top:80px;display:flex;gap:38px;font-family:"Montserrat",sans-serif;font-size:15px;color:var(--white);text-transform:uppercase}
.main-nav .active{color:#c98a63}

/* hero */
.hero{position:absolute;left:0;top:119px;width:1200px;height:687px;background:radial-gradient(ellipse at 70% 45%,#8a8a6a 0%,#4f5d33 30%,#2b3a1c 62%,#141c0d 100%)}
.hero-title{position:absolute;left:110px;top:330px;font-family:"Montserrat",sans-serif;font-weight:800;font-size:74px;color:var(--white)}
.hero-text{position:absolute;left:111px;top:420px;width:520px;font-family:"Montserrat",sans-serif;font-size:15.5px;line-height:35px;color:var(--white)}
.btn{position:absolute;background:var(--brown);color:var(--white);font-family:"Montserrat",sans-serif;font-weight:600;font-size:15px;display:flex;align-items:center;justify-content:center;text-transform:uppercase}

.section-title{position:absolute;font-family:"Montserrat",sans-serif;font-weight:700;font-size:44px;text-transform:uppercase;color:var(--ink)}
.section-sub{position:absolute;font-family:"Montserrat",sans-serif;font-size:16px;line-height:28px;color:var(--muted)}

/* product cards */
.product{position:absolute;width:236px}
.product-img{width:236px;height:258px;box-shadow:0 0 4px rgba(0,0,0,.15)}
.product-name{margin:20px 0 0 3px;font-family:"Montserrat",sans-serif;font-weight:500;font-size:15px;text-transform:uppercase}
.product-desc{margin:8px 0 0 3px;font-size:12.5px;line-height:22px;color:#555}
.product-price{margin:8px 0 0 6px;font-family:"Montserrat",sans-serif;font-size:17px}
.cart-badge{position:absolute;right:17px;top:18px;width:38px;height:38px;border-radius:50%;background:var(--brown);display:flex;align-items:center;justify-content:center}
.on-brown .product-name,.on-brown .product-desc,.on-brown .product-price{color:var(--white)}
.on-brown .product-price{font-weight:600}

.divider{position:absolute;left:111px;width:978px;height:1px;background:var(--line)}

/* offers */
.offer-box{position:absolute;left:111px;top:1640px;width:978px;height:454px;background:var(--white);box-shadow:0 0 8px rgba(0,0,0,.15)}
.offer-text{position:absolute;left:134px;width:490px;font-size:13px;line-height:27.5px;color:var(--muted)}

/* best seller */
.band{position:absolute;left:0;top:2218px;width:1200px;height:633px;background:var(--brown-band)}

/* news */
.news-card{position:absolute;top:3008px;width:318px;height:412px;background:var(--white);box-shadow:0 0 6px rgba(0,0,0,.15)}
.news-img{position:absolute;left:6px;top:6px;width:306px;height:194px}
.news-title{position:absolute;left:14px;top:233px;font-family:"Montserrat",sans-serif;font-weight:500;font-size:14.5px;text-transform:uppercase}
.news-text{position:absolute;left:14px;top:266px;width:295px;font-size:12.5px;line-height:23.5px;color:#444}
.news-meta{position:absolute;left:0;top:355px;width:318px;border-top:1px solid var(--line);padding:20px 28px 0 14px;display:flex;justify-content:space-between;font-size:12.5px;color:#444}

/* features */
.feature{position:absolute;top:3572px;width:200px;text-align:center;font-family:"Roboto",sans-serif;font-size:15.5px;line-height:26px;color:#444;text-transform:uppercase}
.feature svg{display:block;margin:0 auto 8px}

/* footer */
.site-footer{position:absolute;left:0;top:3739px;width:1200px;height:305px;background:var(--black);color:var(--white)}
.footer-nav{position:absolute;right:110px;top:56px;display:flex;gap:38px;font-family:"Montserrat",sans-serif;font-size:15px;text-transform:uppercase}
.contact{position:absolute;display:flex;gap:22px;align-items:flex-start}
.contact .ring{width:54px;height:54px;border:1px solid #aaa;border-radius:50%;display:flex;align-items:center;justify-content:center;flex:none}
.contact .label{font-family:"Montserrat",sans-serif;font-size:15px;text-transform:uppercase;margin-top:-2px}
.contact .value{font-size:15px;line-height:24px;margin-top:4px;color:#ddd}
.footer-bottom{position:absolute;left:0;top:262px;width:1200px;font-size:15px;text-align:center}
.pay{position:absolute;top:255px;width:42px;height:28px;border-radius:3px}
</style>
</head>
<body>

<header class="site-header">
  <div class="topbar">
    <div class="topbar-links">
      <span><svg width="14" height="14" viewBox="0 0 14 14"><circle cx="7" cy="7" r="6" fill="none" stroke="#fff" stroke-width="1.4"/><circle cx="7" cy="5.5" r="2" fill="#fff"/></svg>LOG IN</span>
      <span><svg width="14" height="14" viewBox="0 0 14 14"><circle cx="7" cy="7" r="6" fill="none" stroke="#fff" stroke-width="1.4"/><circle cx="7" cy="5.5" r="2" fill="#fff"/></svg>SIGN UP</span>
      <span><svg width="16" height="14" viewBox="0 0 16 14"><path d="M1 1h3l2 8h7l2-6H5" fill="none" stroke="#fff" stroke-width="1.6"/><circle cx="7" cy="12" r="1.3" fill="#fff"/><circle cx="12" cy="12" r="1.3" fill="#fff"/></svg>(0)</span>
      <span style="margin-left:10px"><svg width="14" height="14" viewBox="0 0 14 14"><circle cx="6" cy="6" r="4.2" fill="none" stroke="#fff" stroke-width="2"/><path d="M9 9l4 4" stroke="#fff" stroke-width="2"/></svg></span>
    </div>
  </div>
  <div class="brand" style="left:172px;top:48px;font-size:17px"><span class="dot"></span>VERDANCE</div>
  <nav class="main-nav">
    <span class="active">Home</span><span>About</span><span>Products</span><span>Reviews</span><span>Blog</span><span>Contact Us</span>
  </nav>
</header>

<section class="hero" role="img" aria-label="Close-up photograph of a frosted hemp flower">
</section>
<h1 class="hero-title">DELTA 8</h1>
<p class="hero-text">Lorem ipsum dolor sit amet, consectetur adipiscing elit, sed do eiusmod tempor incididunt ut labore et dolore magna aliqua.</p>
<a class="btn" style="left:111px;top:504px;width:156px;height:49px">Shop Now</a>

<!-- our products -->
<h2 class="section-title center" style="top:897px;text-align:center">Our Products</h2>
<p class="section-sub center" style="top:957px;text-align:center">Lorem ipsum dolor sit amet, consectetur adipiscing elit,<br>sed do eiusmod tempor incididunt ut labore et</p>

<div class="product" style="left:110px;top:1054px">
  <div class="product-img" role="img" aria-label="Green product pouch with hemp flower" style="background:radial-gradient(circle at 50% 50%,#3f8a2c 0%,#5da43f 22%,#e4e4e4 40%)"></div>
  <div class="product-name">Product 1</div>
  <div class="product-desc">Lorem ipsum dolor sit amet, adipiscing elit, sed do eiusmod tempor</div>
  <div class="product-price">$125.00</div>
</div>
<div class="product" style="left:357px;top:1054px">
  <div class="product-img" role="img" aria-label="Green product pouch with colorful gummies" style="background:radial-gradient(circle at 50% 50%,#3f8a2c 0%,#5da43f 22%,#e4e4e4 40%)"></div>
  <div class="cart-badge"><svg width="18" height="16" viewBox="0 0 16 14"><path d="M1 1h3l2 8h7l2-6H5" fill="none" stroke="#fff" stroke-width="1.8"/><circle cx="7" cy="12" r="1.4" fill="#fff"/><circle cx="12" cy="12" r="1.4" fill="#fff"/></svg></div>
  <div class="product-name">Product 2</div>
  <div class="product-desc">Lorem ipsum dolor sit amet, adipiscing elit, sed do eiusmod tempor</div>
  <div class="product-price">$125.00</div>
</div>
<div class="product" style="left:604px;top:1054px">
  <div class="product-img" role="img" aria-label="Black product pouch with hemp flower" style="background:radial-gradient(circle at 50% 50%,#2a2a2a 0%,#555 22%,#e4e4e4 40%)"></div>
  <div class="product-name">Product 3</div>
  <div class="product-desc">Lorem ipsum dolor sit amet, adipiscing elit, sed do eiusmod tempor</div>
  <div class="product-price">$125.00</div>
</div>
<div class="product" style="left:851px;top:1054px">
  <div class="product-img" role="img" aria-label="Oil bottles beside a hemp leaf" style="background:radial-gradient(circle at 50% 55%,#8a4d1c 0%,#5e8a38 25%,#ffffff 45%)"></div>
  <div class="product-name">Product 4</div>
  <div class="product-desc">Lorem ipsum dolor sit amet, adipiscing elit, sed do eiusmod tempor</div>
  <div class="product-price">$125.00</div>
</div>

<div class="divider" style="top:1536px"></div>

<!-- our offers -->
<div class="abs" style="left:1003px;top:1592px;width:150px;height:150px;border-radius:50%;background:var(--yellow)"></div>
<div class="offer-box"></div>
<h2 class="heading abs" style="left:136px;top:1685px;font-size:43px">Our Offers</h2>
<div class="abs" style="left:137px;top:1745px;width:73px;height:5px;background:#f2c12e"></div>
<p class="offer-text" style="top:1777px">Lorem ipsum dolor sit amet, consectetur adipiscing elit, sed do eiusmod tempor incididunt ut labore et dolore magna aliqua. Ut enim ad minim veniam, quis nostrud exercitation ullamco laboris nisi ut aliquip ex ea commodo consequat. Duis aute irure dolor in reprehenderit in voluptate velit esse cillum</p>
<p class="offer-text" style="top:1914px">Lorem ipsum dolor sit amet, consectetur adipiscing elit, sed do eiusmod tempor incididunt ut labore et dolore magna aliqua.</p>
<a class="btn" style="left:134px;top:1992px;width:154px;height:50px">Shop Now</a>
<div class="abs" role="img" aria-label="Purple hemp flower close-up" style="left:668px;top:1654px;width:408px;height:428px;background:radial-gradient(circle at 50% 50%,#4a2a6a 0%,#8a3fb0 30%,#c65ad8 55%,#b98ae0 80%,#d7c0ee 100%)"></div>
<svg class="abs" style="left:80px;top:2058px" width="70" height="70" viewBox="0 0 70 70"><polygon points="3,40 54,5 66,66" fill="none" stroke="var(--brown)" stroke-width="2"/></svg>

<!-- best seller -->
<section class="band" role="img" aria-label="Brown band with faint hemp leaf backdrop"></section>
<h2 class="section-title center" style="top:2255px;text-align:center;color:var(--white)">Best Seller</h2>
<p class="section-sub center" style="top:2314px;text-align:center;color:var(--white)">Lorem ipsum dolor sit amet, consectetur adipiscing elit,<br>sed do eiusmod tempor incididunt ut labore et</p>

<div class="product on-brown" style="left:110px;top:2413px">
  <div class="product-img" role="img" aria-label="Sugar-coated leaf-shaped gummy" style="height:255px;background:radial-gradient(circle at 50% 50%,#f1d24a 0%,#f4c53a 28%,#ee6a6a 55%,#f7f2f2 80%)"></div>
  <div class="product-name">Product 1</div>
  <div class="product-desc">Lorem ipsum dolor sit amet, adipiscing elit, sed do eiusmod tempor</div>
  <div class="product-price">$125.00</div>
</div>
<div class="product on-brown" style="left:357px;top:2413px">
  <div class="product-img" role="img" aria-label="Hemp plant sprig on white" style="height:255px;background:radial-gradient(circle at 50% 50%,#4c7a2a 0%,#6f9e45 30%,#ffffff 60%)"></div>
  <div class="cart-badge"><svg width="18" height="16" viewBox="0 0 16 14"><path d="M1 1h3l2 8h7l2-6H5" fill="none" stroke="#fff" stroke-width="1.8"/><circle cx="7" cy="12" r="1.4" fill="#fff"/><circle cx="12" cy="12" r="1.4" fill="#fff"/></svg></div>
  <div class="product-name">Product 2</div>
  <div class="product-desc">Lorem ipsum dolor sit amet, adipiscing elit, sed do eiusmod tempor</div>
  <div class="product-price">$125.00</div>
</div>
<div class="product on-brown" style="left:604px;top:2413px">
  <div class="product-img" role="img" aria-label="Dropper bottle with hemp leaves" style="height:255px;background:radial-gradient(circle at 50% 55%,#5b2f14 0%,#3f7a2a 25%,#ffffff 50%)"></div>
  <div class="product-name">Product 3</div>
  <div class="product-desc">Lorem ipsum dolor sit amet, adipiscing elit, sed do eiusmod tempor</div>
  <div class="product-price">$125.00</div>
</div>
<div class="product on-brown" style="left:851px;top:2413px">
  <div class="product-img" role="img" aria-label="Oil vials with hemp leaves and seeds" style="height:255px;background:radial-gradient(circle at 50% 45%,#c9a32a 0%,#5f9038 30%,#ffffff 58%)"></div>
  <div class="product-name">Product 4</div>
  <div class="product-desc">Lorem ipsum dolor sit amet, adipiscing elit, sed do eiusmod tempor</div>
  <div class="product-price">$125.00</div>
</div>

<!-- latest news -->
<h2 class="section-title center" style="top:2926px;text-align:center">Latest News</h2>

<article class="news-card" style="left:111px">
  <div class="news-img" role="img" aria-label="Gloved hands trimming hemp flower" style="background:linear-gradient(135deg,#8a8a88 0%,#5e6d3e 50%,#3f4a2a 100%)"></div>
  <h3 class="news-title">Lorem ipsum dolor sit amet</h3>
  <p class="news-text">Sed ut perspiciatis unde omnis iste natus error sit voluptatem accusantium laudantium, totam rem aperiam, eaque ipsa quae</p>
  <div class="news-meta"><span>145 views</span><span>♡ 55</span></div>
</article>
<article class="news-card" style="left:441px">
  <div class="news-img" role="img" aria-label="Glass jars of hemp flower" style="background:linear-gradient(135deg,#2a2a24 0%,#7d8a6a 45%,#d5d8cf 100%)"></div>
  <h3 class="news-title">Lorem ipsum dolor sit amet</h3>
  <p class="news-text">Sed ut perspiciatis unde omnis iste natus error sit voluptatem accusantium laudantium, totam rem aperiam, eaque ipsa quae</p>
  <div class="news-meta"><span>145 views</span><span>♡ 55</span></div>
</article>
<article class="news-card" style="left:770px">
  <div class="news-img" role="img" aria-label="Gloved hand tending hemp plants in a grow room" style="background:linear-gradient(135deg,#3d6a25 0%,#6fa043 50%,#c8d8b0 100%)"></div>
  <h3 class="news-title">Lorem ipsum dolor sit amet</h3>
  <p class="news-text">Sed ut perspiciatis unde omnis iste natus error sit voluptatem accusantium laudantium, totam rem aperiam, eaque ipsa quae</p>
  <div class="news-meta"><span>145 views</span><span>♡ 55</span></div>
</article>

<div class="divider" style="top:3508px"></div>

<!-- features -->
<div class="feature" style="left:100px">
  <svg width="64" height="64" viewBox="0 0 64 64" fill="none" stroke="#222" stroke-width="2"><circle cx="32" cy="32" r="27" stroke-dasharray="6 3"/><circle cx="32" cy="32" r="19"/><path d="M24 40l16-16"/><circle cx="25" cy="25" r="3"/><circle cx="39" cy="39" r="3"/></svg>
  Deals and Promotion
</div>
<div class="feature" style="left:310px">
  <svg width="64" height="64" viewBox="0 0 64 64" fill="none" stroke="#222" stroke-width="2"><rect x="8" y="8" width="42" height="34" rx="2"/><path d="M32 24l14 5v10c0 9-6 15-14 18-8-3-14-9-14-18V29z"/><path d="M26 40l4 4 8-8"/></svg>
  Secure Payments
</div>
<div class="feature" style="left:522px">
  <svg width="70" height="64" viewBox="0 0 70 64" fill="none" stroke="#222" stroke-width="2"><rect x="4" y="18" width="38" height="26"/><path d="M42 26h12l8 10v8H42"/><circle cx="16" cy="48" r="5"/><circle cx="52" cy="48" r="5"/><path d="M16 31l5 5 10-10"/></svg>
  Free Shipping
</div>
<div class="feature" style="left:739px">
  <svg width="64" height="64" viewBox="0 0 64 64" fill="none" stroke="#222" stroke-width="2"><path d="M32 30L10 38v16l22 8 22-8V38z"/><path d="M10 38l22 8 22-8M32 46v16"/><path d="M32 28c-6-7-9-11-9-15a9 9 0 0118 0c0 4-3 8-9 15z"/><circle cx="32" cy="13" r="3"/></svg>
  Track Your Order
</div>
<div class="feature" style="left:929px">
  <svg width="64" height="64" viewBox="0 0 64 64" fill="none" stroke="#222" stroke-width="2"><path d="M14 34v-6a18 18 0 0136 0v6"/><rect x="10" y="32" width="9" height="16" rx="3"/><rect x="45" y="32" width="9" height="16" rx="3"/><path d="M50 48c0 6-6 9-14 9"/><circle cx="33" cy="57" r="3"/></svg>
  24/7 Customer<br>Services
</div>

<!-- footer -->
<footer class="site-footer">
  <div class="brand" style="left:150px;top:47px;font-size:17px"><span class="dot"></span>VERDANCE</div>
  <nav class="footer-nav"><span>Home</span><span>About</span><span>Products</span><span>Reviews</span><span>Blog</span><span>Contact Us</span></nav>

  <div class="contact" style="left:264px;top:141px">
    <div class="ring"><svg width="22" height="22" viewBox="0 0 24 24" fill="none" stroke="#fff" stroke-width="1.6"><path d="M5 3h4l2 5-3 2a12 12 0 006 6l2-3 5 2v4a2 2 0 01-2 2C10 21 3 14 3 5a2 2 0 012-2z"/></svg></div>
    <div><div class="label">Phone</div><div class="value">123-456-7890</div></div>
  </div>
  <div class="contact" style="left:524px;top:141px">
    <div class="ring"><svg width="20" height="22" viewBox="0 0 20 24"><path d="M10 23C4 15 2 12 2 8a8 8 0 0116 0c0 4-2 7-8 15z" fill="#fff"/><circle cx="10" cy="8" r="3" fill="#000"/></svg></div>
    <div><div class="label">Address</div><div class="value">123,Lorem ipsum dolor sit amet,<br>consectetur adipiscing</div></div>
  </div>
  <div class="contact" style="left:901px;top:124px">
    <div class="ring" style="margin-top:17px"><svg width="22" height="18" viewBox="0 0 22 18" fill="none" stroke="#fff" stroke-width="1.5"><rect x="1" y="1" width="20" height="16" rx="1"/><path d="M1 2l10 8 10-8"/></svg></div>
    <div><div class="label">Email</div><div class="value">hello@verdancehemp.com</div></div>
  </div>

  <span class="abs" style="left:110px;top:266px;width:12px;height:12px;border-radius:50%;background:#fff"></span>
  <span class="abs" style="left:138px;top:266px;width:12px;height:12px;border:2px solid #fff"></span>
  <div class="footer-bottom">© 2021 All Rights Reserved</div>
  <span class="pay" style="left:950px;background:#b23a2a"></span>
  <span class="pay" style="left:1000px;background:#2a3f9a"></span>
  <span class="pay" style="left:1052px;background:#4f8cc9"></span>
</footer>

</body>
</html>
```